International business needs business cards

Our company, DRV Ventures Inc. is in the business of supplying a range construction products with particular emphasis on CEMENT. We have developed our own brand - TORVAN SUPPLIES - with which to infiltrate the market. We are launching our brand of cement (TORVAN Type IS Cement) into the Caribbean which is unlike anything this market has ever seen. A monopoly has existed here for the past 60-odd years and the market has now opened to allow the importation of other brands and consumers are anxious and ready for change/improvement. We are very excited to be launching and want to make a great first impression. We will be conducting workshops and seminars (from government level to the hardware store owners) and we want our business card to give us the strong, confident introduction that we need.

Target Market(s)

construction; builders; engineers; home owners

Industry/Entity Type

Construction

Contact Information for Business Card

Marisol Depree
CEO
cell # 1 555 4180736
Ground floor,Lindell Plaza Suite 2734
George Town,Grand Cayman
Cayman Islands,KY1-4823
EMAIL: m.depree@drvventuresinc.example
web site drvventuresinc.example

COMPANY: skype info drv.ventures.example

second card
Yvette Brannock-Depree
CFO
CELL# 1 555 607 3941
George Town,Grand Cayman
Cayman Islands,KY1-4823
EMAIL: y.brannockdepree@drvventuresinc.example
website drvventuresinc.example

Requirements
Must have
• Business cards must display BOTH logos - DRV is the company and TORVAN is the brand.

```html
<!DOCTYPE html>
<html lang="en">
<head>
<meta charset="utf-8">
<title>DRV Ventures Inc. – Business Card</title>
<link href="https://fonts.googleapis.com/css2?family=Open+Sans:wght@400;600;700&display=swap" rel="stylesheet">
<style>
  :root {
    --brand-red: #7b1518;
    --ink: #141414;
    --paper: #ffffff;
    --stage: #e4e4e2;
    --accent-tan: #b48a6c;
  }
  * { margin: 0; padding: 0; box-sizing: border-box; }
  html, body { width: 1200px; height: 900px; overflow: hidden; }
  body {
    background: var(--stage);
    font-family: "Open Sans", Arial, sans-serif;
    display: flex;
    flex-direction: column;
    align-items: center;
    justify-content: center;
    gap: 18px;
  }
  .card {
    position: relative;
    width: 720px;
    height: 411px;
    background: var(--paper);
    overflow: hidden;
  }

  /* Front */
  .card-front {
    display: flex;
    flex-direction: column;
    align-items: center;
    justify-content: center;
    gap: 40px;
  }
  .company-mark {
    display: flex;
    align-items: center;
    gap: 16px;
  }
  .mark-square {
    width: 70px;
    height: 70px;
    background: var(--brand-red);
  }
  .company-name {
    font-weight: 700;
    font-size: 40px;
    color: var(--ink);
    letter-spacing: 0.5px;
  }
  .brand-mark {
    display: flex;
    align-items: center;
    gap: 10px;
  }
  .brand-circle {
    width: 26px;
    height: 26px;
    border-radius: 50%;
    background: #555;
  }
  .brand-name {
    font-weight: 600;
    font-size: 20px;
    letter-spacing: 2px;
    color: #555;
  }

  /* Back */
  .card-back .back-shape {
    position: absolute;
    inset: 0;
    width: 100%;
    height: 100%;
  }
  .back-mark {
    position: absolute;
    left: 40px;
    top: 120px;
    display: flex;
    align-items: center;
    gap: 12px;
  }
  .back-mark .mark-square { width: 56px; height: 56px; }
  .back-mark .company-name { font-size: 30px; color: var(--brand-red); }
  .contact {
    position: absolute;
    right: 38px;
    top: 88px;
    text-align: right;
    color: var(--paper);
    font-size: 16.5px;
    line-height: 1.3;
  }
  .contact-name { font-size: 20px; font-weight: 600; }
  .contact-role { font-size: 15px; margin-bottom: 14px; }
  .contact-address { margin-bottom: 14px; }
  .contact-line {
    display: flex;
    justify-content: flex-end;
    align-items: center;
    gap: 10px;
  }
  .contact-icon { width: 13px; height: 13px; flex: none; }
</style>
</head>
<body>

  <section class="card card-front">
    <div class="company-mark">
      <span class="mark-square"></span>
      <span class="company-name">DRV Ventures Inc.</span>
    </div>
    <div class="brand-mark">
      <span class="brand-circle"></span>
      <span class="brand-name">TORVAN SUPPLIES</span>
    </div>
  </section>

  <section class="card card-back">
    <svg class="back-shape" viewBox="0 0 720 411" preserveAspectRatio="none" aria-hidden="true">
      <path d="M372 0 C 356 170 290 330 150 411 L132 411 C 270 330 338 170 350 0 Z" fill="var(--ink)"/>
      <path d="M384 0 C 368 170 302 330 162 411 L720 411 L720 0 Z" fill="var(--brand-red)"/>
    </svg>

    <div class="back-mark">
      <span class="mark-square"></span>
      <span class="company-name">DRV</span>
    </div>

    <div class="contact">
      <div class="contact-name">Marisol Depree</div>
      <div class="contact-role">CEO</div>
      <div class="contact-address">
        Ground floor, Lindell Plaza Suite<br>
        2734 George Town, Grand Cayman<br>
        Cayman Islands, KY1-4823
      </div>
      <div class="contact-line">1 555 4180736
        <svg class="contact-icon" viewBox="0 0 12 12"><rect x="3" y="0.5" width="6" height="11" rx="1" fill="none" stroke="#fff" stroke-width="1.2"/><circle cx="6" cy="9.5" r="0.8" fill="#fff"/></svg>
      </div>
      <div class="contact-line">m.depree@drvventuresinc.example
        <svg class="contact-icon" viewBox="0 0 12 12"><rect x="0.5" y="2.5" width="11" height="7" fill="#fff"/><path d="M0.5 2.5 L6 6.5 L11.5 2.5" fill="none" stroke="var(--brand-red)" stroke-width="1"/></svg>
      </div>
      <div class="contact-line">www.drvventuresinc.example
        <svg class="contact-icon" viewBox="0 0 12 12"><circle cx="6" cy="6" r="5.5" fill="#fff"/><path d="M1 6 H11 M6 0.5 C3 3 3 9 6 11.5 M6 0.5 C9 3 9 9 6 11.5" fill="none" stroke="var(--brand-red)" stroke-width="0.8"/></svg>
      </div>
    </div>
  </section>

</body>
</html>
```